Smart, Classy, Conservative looking Legal Letterhead

I need a letterhead that when you look at it it "says to you " this is a well established law firm with very smart lawyers, which will one day be appearing before the Supreme Court of the USA. All information about the Law firm should appear at the top of the page. please no information in the footer.

Industry/Entity Type

Legal

Requirements
Must have
• The name of the law firm, both addresses, phone number and fax,, The names of the attorneys, the website.
• Fields that get changed such as the date, VIA, Address of who the letter is going to,
• Re, Index,
• should have a clean neat look, sleek
Nice to have
• some color would be nice. A logo of some sort could be nice as well. Maybe a single S or interlocking M's For Merriton and Merriton.
Should not have
• not too modern looking.

```html
<!DOCTYPE html>
<html lang="en">
<head>
<meta charset="utf-8">
<title>Merriton &amp; Merriton Letterhead</title>
<link rel="stylesheet" href="https://fonts.googleapis.com/css2?family=Cinzel:wght@700&family=Tinos:ital,wght@0,400;0,700;1,400&display=swap">
<style>
  :root {
    --backdrop: #d9d9d9;
    --paper: #ffffff;
    --ink: #111111;
    --gold: #b8a21a;
    --gold-soft: #e9e0a0;
  }
  * { margin: 0; padding: 0; box-sizing: border-box; }
  html, body { width: 1200px; height: 900px; overflow: hidden; background: var(--backdrop); }
  body { position: relative; font-family: "Tinos", "Times New Roman", serif; color: var(--ink); }
  .letterhead {
    position: absolute; left: 290px; top: 14px; width: 620px; height: 871px;
    background: var(--paper); font-size: 10.5px; line-height: 12.4px;
  }
  .letterhead > * { position: absolute; }
  .firm-mark { left: 22px; top: 30px; width: 72px; text-align: center; color: var(--gold);
    font-weight: 700; font-size: 12px; line-height: 15px; }
  .firm-mark-dot { display: block; width: 30px; height: 30px; margin: 0 auto 6px; border-radius: 50%; background: var(--gold); }
  .firm-block { left: 140px; top: 24px; width: 340px; text-align: center; }
  .firm-name { font-family: "Cinzel", "Times New Roman", serif; font-weight: 700; font-size: 20px; line-height: 26px; letter-spacing: 0.3px; }
  .firm-tagline { font-family: "Cinzel", "Times New Roman", serif; font-weight: 700; font-size: 16px; line-height: 20px; }
  .firm-offices { display: flex; justify-content: center; gap: 10px; margin-top: 3px; font-size: 10.5px; line-height: 12px; }
  .firm-web { margin-top: 5px; font-size: 10.5px; }
  .attorney-list { right: 24px; top: 27px; text-align: right; font-weight: 700; font-size: 10.5px; line-height: 12.2px; list-style: none; }
  .letter-date { left: 110px; top: 118px; font-style: italic; font-size: 17px; line-height: 20px; }
  .recipient { left: 23px; top: 152px; }
  .delivery { font-weight: 700; }
  .reference { left: 71px; top: 245px; display: grid; grid-template-columns: 38px auto; }
  .reference dt { font-weight: 700; }
  .salutation { left: 23px; top: 289px; }
  .letter-body { left: 23px; top: 310px; width: 575px; }
  .letter-body p { margin-bottom: 12.4px; }
  .letter-body p:first-child { text-indent: 58px; }
  .closing { left: 109px; top: 402px; }
  .copy-to { left: 23px; bottom: 21px; }
  .copy-to strong { font-weight: 700; }
</style>
</head>
<body>
  <article class="letterhead">
    <div class="firm-mark"><span class="firm-mark-dot"></span>Merriton<br>&amp;<br>Merriton</div>

    <header class="firm-block">
      <h1 class="firm-name">MERRITON &amp; MERRITON</h1>
      <p class="firm-tagline">ATTORNEYS AT LAW</p>
      <div class="firm-offices">
        <address>414 MADE UP STREET<br>TOWN, STATE 39440</address>
        <address>414 MADE UP STREET<br>TOWN, STATE 39440</address>
      </div>
      <p class="firm-web">WWW.WEBSITE.COM</p>
    </header>

    <ul class="attorney-list">
      <li>Daniel A. Merriton</li>
      <li>Edward L. Harlow</li>
      <li>Thomas R. Whitfield</li>
      <li>Margaret E. Colton</li>
      <li>Philip J. Ashworth</li>
      <li>Helen M. Garrison</li>
    </ul>

    <p class="letter-date">July 1st 2015</p>

    <address class="recipient" style="font-style:normal">
      <span class="delivery">VIA FEDEX</span><br>
      Hon. Fake Judge Name Here<br>
      United States District Court, E.D.N.Y<br>
      200 Civic Plaza<br>
      Courtroom 99999<br>
      Harborview, NY 11700-0000
    </address>

    <dl class="reference">
      <dt>Re:</dt><dd>XXXXXXXXXXXXXXXXXXXXXXXXXXXXXXXX</dd>
      <dt>Index:</dt><dd>XXXXXXXXXXXXXXXXXXXXXXXXXXXXXXX</dd>
    </dl>

    <p class="salutation">Your Honour,</p>

    <div class="letter-body">
      <p>Pursuant to Your Honor's Individual Practises Rule III(C)(3), enclosed please find a courtesy copy of Plaintiffs Revised. Lorem ipsum dolor sit amet, consectetur adipiscing elit, sed do eiusmod tempor incididunt ut labore et dolore magna aliqua. Ut enim ad minim veniam, quis nostrud exercitation ullamco laboris nisi ut aliquip ex ea commodo consequat.</p>
      <p>Duis aute irure dolo in reprehenderit in voluptate velit esse cillum dolore eu fugiat nulla pariatur. Excepteur sint occaecat cupidatat non proident, sunt in culpa qui officia deserunt mollit anim id est laborum.</p>
    </div>

    <p class="closing">Respectfully,<br>Daniel A. Merriton</p>

    <p class="copy-to"><strong>CC:</strong> Fake opposing counsel name here</p>
  </article>
</body>
</html>
```